How likely are people to engage in social distancing? We need a good illustration to show the data!

We surveyed U.S. adults March 20th - 24th, 2020 and asked how likely they were to engage in social distancing (and other COVID-19 related health behaviors). What did the survey find? Basically, most people intend to engage in social distancing behaviors (e.g., avoiding large crowds) and other behaviors that reduce the spread of COVID-19 (e.g., washing hands at least 20 seconds). When most people intend to engage in a behavior, then public health professionals try to leverage that to move more people to act.
Now we need innovative and professional images that attempt to communicate one or all of these findings. The specific findings are nicely summarized in the attached document. For example, 82% of participants intend to engage in social distancing.
What sort of visual are we looking for? Our preference is for an original illustration (or set of illustrations). Our preference is for (creative and powerful illustrations, but we are also open to the creative and well-executed infographics.
We need these images fast . We will award monetary prizes to the 3 best designs. If we like more than that, then we might purchase more (e.g., in past contests, we have purchased as many as 30 designs).
What we will need:
(1) The illustrations must be original and we will need the photoshop and/or illustrator files for all artwork.
(2) You can illustrate all of the findings or just one of them. We need creative approaches that do a lucid job of bringing the data to life. Most people intend to engage in these behaviors. How to communicate that? Republicans and Democrats do not differ in their intentions; how to communicate that?
(3) The illustration should say, somewhere: "Based on a survey of 400 U.S. adults conducted March 20 - 24th, 2020."

U.S. Adults

• Original illustrations based on the findings of the survey (see attached document).

```html
<!DOCTYPE html>
<html lang="en">
<head>
<meta charset="utf-8">
<title>How Likely Are People to Engage in Social Distancing</title>
<link href="https://fonts.googleapis.com/css2?family=Arvo:wght@700&family=Questrial&family=Nunito:wght@900&display=swap" rel="stylesheet">
<style>
  :root {
    --bg: #521e3c;
    --bg-glow: #5e2446;
    --white: #ffffff;
    --card-top: #9a1c5b;
    --card-mid: #c17e99;
    --card-bottom: #e6c4cf;
    --pie-top: #9e1d5f;
    --pie-side: #6b003a;
    --slice-top: #cecece;
    --slice-side: #858585;
    --value-shadow: #8d8d8d;
    --ink: #1c1a1c;
    --figure-blue: #1a73b8;
    --figure-white: #f6f6f6;
    --figure-grey: #a9a9a9;
    --skin: #e8a996;
    --friend-orange: #f26522;
    --friend-green: #3bb34a;
    --friend-pink: #ea7bb0;
    --friend-brown: #5a3324;
    --sign-red: #e52530;
  }
  * { margin: 0; padding: 0; box-sizing: border-box; }
  html, body { width: 800px; height: 1200px; overflow: hidden; }
  body {
    position: relative;
    background: radial-gradient(ellipse at 20% 15%, var(--bg-glow), var(--bg) 60%);
    color: var(--white);
    font-family: "Questrial", sans-serif;
  }
  .headline {
    position: absolute;
    top: 26px; left: 0; width: 800px;
    text-align: center;
    font-family: "Arvo", serif;
    font-weight: 700;
    font-size: 34px;
    line-height: 40px;
    letter-spacing: 1.8px;
    text-transform: uppercase;
  }
  .intro {
    position: absolute;
    left: 32px; width: 736px;
    font-size: 21.5px;
    line-height: 26.7px;
    letter-spacing: 0.6px;
  }
  .intro p { white-space: nowrap; }
  .intro--method { top: 137px; }
  .intro--findings { top: 243px; }
  .intro .justified { text-align: justify; text-align-last: justify; white-space: normal; }
  .section-title {
    position: absolute;
    top: 454px; left: 0; width: 800px;
    text-align: center;
    font-family: "Nunito", sans-serif;
    font-weight: 900;
    font-size: 30px;
    letter-spacing: 0.6px;
  }
  .section-rule {
    position: absolute;
    top: 511px; left: 212px;
    width: 376px; height: 2px;
    background: var(--white);
  }
  .stat-card {
    position: absolute;
    width: 164px; height: 239px;
    border-radius: 18px 18px 58px 58px;
    background: linear-gradient(180deg, var(--card-top) 0%, var(--card-mid) 48%, var(--card-bottom) 100%);
    overflow: hidden;
  }
  .stat-card__title {
    position: absolute;
    top: 6px; left: 0; width: 100%;
    text-align: center;
    font-family: "Nunito", sans-serif;
    font-weight: 900;
    font-size: 16px;
    line-height: 19px;
    letter-spacing: 0.4px;
    white-space: nowrap;
  }
  .stat-card__title--small { font-size: 12.5px; line-height: 15px; top: 9px; }
  .stat-card__title--medium { font-size: 14.5px; line-height: 17px; top: 7px; }
  .stat-card__art {
    position: absolute;
    top: 48px; left: 18px;
    width: 128px; height: 78px;
    border-radius: 50% / 45%;
  }
  .row-2 .stat-card__art { top: 52px; }
  .art--distancing { background: linear-gradient(90deg, var(--figure-white) 0%, var(--figure-white) 18%, var(--ink) 42%, var(--ink) 58%, var(--figure-blue) 82%, var(--figure-blue) 100%); }
  .art--home { background: linear-gradient(90deg, var(--figure-blue) 0%, var(--figure-blue) 22%, var(--ink) 48%, var(--skin) 62%, var(--figure-blue) 100%); }
  .art--crowd { background: radial-gradient(circle at 50% 55%, var(--figure-white) 0%, var(--figure-grey) 40%, var(--ink) 75%, var(--figure-blue) 100%); }
  .art--friends { background: linear-gradient(90deg, var(--friend-pink) 0%, var(--friend-orange) 30%, var(--friend-brown) 62%, var(--friend-green) 85%, var(--friend-green) 100%); }
  .art--spacing { background: linear-gradient(90deg, var(--figure-grey) 0%, var(--ink) 38%, var(--card-mid) 62%, var(--figure-white) 82%, var(--figure-white) 100%); }
  .art--washing { background: radial-gradient(ellipse at 55% 30%, var(--figure-white) 0%, var(--skin) 45%, #d98f7c 100%); }
  .art--sanitizer { background: radial-gradient(ellipse at 50% 60%, var(--figure-white) 0%, var(--figure-white) 30%, var(--sign-red) 70%, #a3171f 100%); }
  .art--touching { background: radial-gradient(circle at 50% 50%, var(--figure-white) 0%, var(--skin) 40%, var(--sign-red) 68%, var(--sign-red) 100%); }
  .stat-card__pie { position: absolute; top: 0; left: 0; }
  .stat-card__value {
    position: absolute;
    top: 133px; left: 0; width: 100%;
    text-align: center;
    font-family: "Nunito", sans-serif;
    font-weight: 900;
    font-size: 31px;
    letter-spacing: 0.5px;
    text-shadow: 2px 2px 0 var(--value-shadow);
  }
  .col-1 { left: 32px; } .col-2 { left: 223px; } .col-3 { left: 413px; } .col-4 { left: 604px; }
  .row-1 { top: 544px; } .row-2 { top: 842px; }
  .source-note {
    position: absolute;
    top: 1136px; left: 0; width: 800px;
    text-align: center;
    font-size: 15px;
    letter-spacing: 0.3px;
  }
</style>
</head>
<body>
  <h1 class="headline">How likely are people to engage in<br>social distancing</h1>

  <div class="intro intro--method">
    <p class="justified">We surveyed 400 U.S. adults from March 20th – 24th, 2020 and asked</p>
    <p>how likely they were to engage in</p>
    <p>social distancing (and other COVID-19 related health behaviors).</p>
  </div>

  <div class="intro intro--findings">
    <p>What did the survey find?</p>
    <p>Basically, most people intend to engage in social distancing</p>
    <p class="justified">(e.g. avoiding large crowds) and other behaviors that reduce the spread</p>
    <p>of COVID-19 (e.g. washing hands at least 20 seconds).</p>
    <p class="justified">When most people intend to engage in a behavior, then public health</p>
    <p>professionals try to leverage that to move more people to act.</p>
  </div>

  <h2 class="section-title">What did the Survey find?</h2>
  <div class="section-rule"></div>

  <div class="stat-card col-1 row-1">
    <div class="stat-card__title">Engage in<br>Social Distancing</div>
    <div class="stat-card__art art--distancing" role="img" aria-label="Three people standing 6 feet apart with arrows between them"></div>
    <svg class="stat-card__pie" width="164" height="239" viewBox="0 0 164 239">
      <path fill="var(--pie-side)" d="M13 170 L13 193 A69 38 0 0 0 151 193 L151 170 A69 38 0 0 1 13 170 Z"/>
      <path fill="var(--slice-side)" d="M82 208 L82 231 A69 38 0 0 1 19.6 209.2 L19.6 186.2 A69 38 0 0 0 82 208 Z"/>
      <ellipse fill="var(--pie-top)" cx="82" cy="170" rx="69" ry="38"/>
      <path fill="var(--slice-top)" d="M82 170 L82 208 A69 38 0 0 1 19.6 186.2 Z"/>
    </svg>
    <div class="stat-card__value">82%</div>
  </div>

  <div class="stat-card col-2 row-1">
    <div class="stat-card__title">Work from<br>Home</div>
    <div class="stat-card__art art--home" role="img" aria-label="Person working on a laptop at a desk with a lamp and a mug"></div>
    <svg class="stat-card__pie" width="164" height="239" viewBox="0 0 164 239">
      <path fill="var(--pie-side)" d="M13 170 L13 193 A69 38 0 0 0 151 193 L151 170 A69 38 0 0 1 13 170 Z"/>
      <path fill="var(--slice-side)" d="M82 208 L82 231 A69 38 0 0 1 13 193 L13 170 A69 38 0 0 0 82 208 Z"/>
      <ellipse fill="var(--pie-top)" cx="82" cy="170" rx="69" ry="38"/>
      <path fill="var(--slice-top)" d="M82 170 L82 208 A69 38 0 0 1 31.7 144 Z"/>
    </svg>
    <div class="stat-card__value">63%</div>
  </div>

  <div class="stat-card col-3 row-1">
    <div class="stat-card__title">Avoid Large<br>Gatherings</div>
    <div class="stat-card__art art--crowd" role="img" aria-label="Dense crowd of small figures"></div>
    <svg class="stat-card__pie" width="164" height="239" viewBox="0 0 164 239">
      <path fill="var(--pie-side)" d="M13 170 L13 193 A69 38 0 0 0 151 193 L151 170 A69 38 0 0 1 13 170 Z"/>
      <path fill="var(--slice-side)" d="M82 208 L82 231 A69 38 0 0 1 26.2 215.3 L26.2 192.3 A69 38 0 0 0 82 208 Z"/>
      <ellipse fill="var(--pie-top)" cx="82" cy="170" rx="69" ry="38"/>
      <path fill="var(--slice-top)" d="M82 170 L82 208 A69 38 0 0 1 26.2 192.3 Z"/>
    </svg>
    <div class="stat-card__value">85%</div>
  </div>

  <div class="stat-card col-4 row-1">
    <div class="stat-card__title">Cancel<br>Social Activities</div>
    <div class="stat-card__art art--friends" role="img" aria-label="Group of friends with arms around each other"></div>
    <svg class="stat-card__pie" width="164" height="239" viewBox="0 0 164 239">
      <path fill="var(--pie-side)" d="M13 170 L13 193 A69 38 0 0 0 151 193 L151 170 A69 38 0 0 1 13 170 Z"/>
      <path fill="var(--slice-side)" d="M82 208 L82 231 A69 38 0 0 1 17.8 207 L17.8 184 A69 38 0 0 0 82 208 Z"/>
      <ellipse fill="var(--pie-top)" cx="82" cy="170" rx="69" ry="38"/>
      <path fill="var(--slice-top)" d="M82 170 L82 208 A69 38 0 0 1 17.8 184 Z"/>
    </svg>
    <div class="stat-card__value">81%</div>
  </div>

  <div class="stat-card col-1 row-2">
    <div class="stat-card__title stat-card__title--small">Put distance between<br>yourself &amp; others</div>
    <div class="stat-card__art art--spacing" role="img" aria-label="Group of people separated 6 ft from one person"></div>
    <svg class="stat-card__pie" width="164" height="239" viewBox="0 0 164 239">
      <path fill="var(--pie-side)" d="M13 170 L13 193 A69 38 0 0 0 151 193 L151 170 A69 38 0 0 1 13 170 Z"/>
      <path fill="var(--slice-side)" d="M82 208 L82 231 A69 38 0 0 1 26.2 215.3 L26.2 192.3 A69 38 0 0 0 82 208 Z"/>
      <ellipse fill="var(--pie-top)" cx="82" cy="170" rx="69" ry="38"/>
      <path fill="var(--slice-top)" d="M82 170 L82 208 A69 38 0 0 1 26.2 192.3 Z"/>
    </svg>
    <div class="stat-card__value">85%</div>
  </div>

  <div class="stat-card col-2 row-2">
    <div class="stat-card__title">Wash Hands<br>atleast 20 Sec</div>
    <div class="stat-card__art art--washing" role="img" aria-label="Soapy hands being washed"></div>
    <svg class="stat-card__pie" width="164" height="239" viewBox="0 0 164 239">
      <path fill="var(--pie-side)" d="M13 170 L13 193 A69 38 0 0 0 151 193 L151 170 A69 38 0 0 1 13 170 Z"/>
      <path fill="var(--slice-side)" d="M82 208 L82 231 A69 38 0 0 1 31.7 219 L31.7 196 A69 38 0 0 0 82 208 Z"/>
      <ellipse fill="var(--pie-top)" cx="82" cy="170" rx="69" ry="38"/>
      <path fill="var(--slice-top)" d="M82 170 L82 208 A69 38 0 0 1 31.7 196 Z"/>
    </svg>
    <div class="stat-card__value">87%</div>
  </div>

  <div class="stat-card col-3 row-2">
    <div class="stat-card__title">Use<br>Hand Sanitizers</div>
    <div class="stat-card__art art--sanitizer" role="img" aria-label="Pump bottle of hand sanitizer"></div>
    <svg class="stat-card__pie" width="164" height="239" viewBox="0 0 164 239">
      <path fill="var(--pie-side)" d="M13 170 L13 193 A69 38 0 0 0 151 193 L151 170 A69 38 0 0 1 13 170 Z"/>
      <path fill="var(--slice-side)" d="M82 208 L82 231 A69 38 0 0 1 26.2 215.3 L26.2 192.3 A69 38 0 0 0 82 208 Z"/>
      <ellipse fill="var(--pie-top)" cx="82" cy="170" rx="69" ry="38"/>
      <path fill="var(--slice-top)" d="M82 170 L82 208 A69 38 0 0 1 26.2 192.3 Z"/>
    </svg>
    <div class="stat-card__value">85%</div>
  </div>

  <div class="stat-card col-4 row-2">
    <div class="stat-card__title stat-card__title--medium">Avoid touching<br>Eyes, Nose &amp; Mouth</div>
    <div class="stat-card__art art--touching" role="img" aria-label="Prohibition sign over an eye, nose and mouth"></div>
    <svg class="stat-card__pie" width="164" height="239" viewBox="0 0 164 239">
      <path fill="var(--pie-side)" d="M13 170 L13 193 A69 38 0 0 0 151 193 L151 170 A69 38 0 0 1 13 170 Z"/>
      <path fill="var(--slice-side)" d="M82 208 L82 231 A69 38 0 0 1 17.8 207 L17.8 184 A69 38 0 0 0 82 208 Z"/>
      <ellipse fill="var(--pie-top)" cx="82" cy="170" rx="69" ry="38"/>
      <path fill="var(--slice-top)" d="M82 170 L82 208 A69 38 0 0 1 17.8 184 Z"/>
    </svg>
    <div class="stat-card__value">81%</div>
  </div>

  <p class="source-note">*Based on a survey of 400 U.S. adults conducted March 20 – 24th, 2020.</p>
</body>
</html>
```